Hip surgeon needs a educative book cover design

I need to re-design my old book cover for its 3rd edition.
It's a small book dedicated to my patients, who underwent total hip replacement. It's meant to help people getting around the basic care after a total hip replacement surgery and getting back to their normal, active life.
The title is: "Morning light rituals: a quiet companion".
I already had a new logo, new stationery and new website design from ArtFolio (please see the attachments).
The final design should be look alike the other fresh new designs. It must communicate health, peacefulness.
I also attached the manual as it looks today for reference.
A5 size.
Just cover and back cover.
Health

```html
<!DOCTYPE html>
<html lang="en">
<head>
<meta charset="utf-8">
<title>Morning light rituals: a quiet companion</title>
<link rel="stylesheet" href="https://fonts.googleapis.com/css2?family=Della+Respira&display=swap">
<style>
  :root {
    --cover-blue: #0036e2;
    --wave-light: rgba(120, 160, 255, 0.55);
    --paper: #ffffff;
    --ink-border: #000000;
    --emblem-dark: #3c3c3c;
    --emblem-mid: #6e6e6e;
    --emblem-light: #a8a8a8;
  }
  html, body {
    margin: 0;
    padding: 0;
    width: 846px;
    height: 1200px;
    overflow: hidden;
    background: var(--paper);
  }
  .cover {
    position: relative;
    width: 846px;
    height: 1200px;
    box-sizing: border-box;
    border: 1px solid var(--ink-border);
    background: var(--paper);
    overflow: hidden;
    font-family: "Della Respira", serif;
  }
  .cover__band {
    position: absolute;
    left: 0;
    top: 0;
    width: 434px;
    height: 100%;
    background: var(--cover-blue);
  }
  .cover__waves {
    position: absolute;
    left: 0;
    top: 250px;
    width: 434px;
    height: 560px;
    background:
      linear-gradient(160deg, rgba(0,54,226,0) 30%, var(--wave-light) 48%, rgba(0,54,226,0) 56%),
      linear-gradient(20deg, rgba(0,54,226,0) 40%, rgba(120,160,255,0.35) 52%, rgba(0,54,226,0) 64%),
      radial-gradient(ellipse 60% 25% at 45% 52%, rgba(130,170,255,0.45), rgba(0,54,226,0) 100%);
  }
  .title-block {
    position: absolute;
    left: 108px;
    top: 108px;
    width: 643px;
    height: 96px;
    background: var(--cover-blue);
    color: var(--paper);
    text-align: center;
  }
  .title-block__title {
    margin: 6px 0 0;
    font-size: 43px;
    font-weight: 400;
    letter-spacing: 0.5px;
    line-height: 1.1;
    text-transform: uppercase;
  }
  .title-block__subtitle {
    margin: 0;
    font-size: 24px;
    letter-spacing: 0.5px;
    -webkit-text-stroke: 0.5px var(--paper);
  }
  .emblem {
    position: absolute;
    left: 312px;
    top: 390px;
    width: 222px;
    height: 222px;
  }
  .emblem__name {
    font-family: "Della Respira", serif;
    font-size: 30px;
    fill: var(--paper);
  }
  .author-block {
    position: absolute;
    left: 95px;
    top: 800px;
    width: 660px;
    height: 96px;
    background: var(--paper);
    display: flex;
    align-items: center;
    justify-content: center;
  }
  .author-block__name {
    margin: 0;
    font-size: 50px;
    color: var(--cover-blue);
    -webkit-text-stroke: 1px var(--cover-blue);
    letter-spacing: 0.5px;
  }
</style>
</head>
<body>
  <main class="cover">
    <div class="cover__band"></div>
    <div class="cover__waves" role="img" aria-label="Fine flowing wave lines in light blue"></div>

    <header class="title-block">
      <h1 class="title-block__title">Morning Light Rituals</h1>
      <p class="title-block__subtitle">-a quiet companion-</p>
    </header>

    <svg class="emblem" viewBox="0 0 222 222" role="img" aria-label="Ferreira Ortho">
      <defs>
        <linearGradient id="emblem-fill" x1="0" y1="0" x2="0" y2="1">
          <stop offset="0" stop-color="#3c3c3c"/>
          <stop offset="0.5" stop-color="#6e6e6e"/>
          <stop offset="1" stop-color="#a8a8a8"/>
        </linearGradient>
      </defs>
      <circle cx="111" cy="111" r="109" fill="url(#emblem-fill)" stroke="#444" stroke-width="3"/>
      <text class="emblem__name" x="111" y="106" text-anchor="middle">Ferreira</text>
      <text class="emblem__name" x="111" y="140" text-anchor="middle">Ortho</text>
    </svg>

    <section class="author-block">
      <p class="author-block__name">Dr. Lucas M. Ferreira</p>
    </section>
  </main>
</body>
</html>
```